Brightway Haus Inc. Business Card Design

Brightway Haus Inc. is in search of a great clean design for our business cards!

Looking to incorporate our full logo and watermark on side one (however, I am open to having the text and watermark separated within the design.)

On side two, I am looking to have contact information (Name, Position, Phone #, Email, Website (www.thebrightwayhaus.ca). Can have the logo and/or watermark as part of the design if applicable.

Please add tagline "Where Shine Counts" on either side 1 or 2. This tagline can be in a sans serif, serif or cursive font as long as it compliments overall design. Capitalization can be title or sentence case depending on how it fits within the design.

Get creative!! Looking for a clean, crisp, premium design! Looking for a glossy card finish with spot UV features when printed. Cards will also be printed with rounded corners. Standard dimensions (3.5 x 2).

Target Market(s)

B2B - primary clients are business owners or property management corporations. (residential jobs are few and far between)

Industry/Entity Type

Business

Contact Information for Business Card

- clean, crisp design
- double sided
- spot UV accents and glossy finish upon printing
- standard business card size (3.5 x 2) with rounded corners
- please see project description for requirements per side

Font styles to use
Sans Serif

Requirements
Must have
• - adequate bleeds with print ready files
• - cohesive design elements between side 1 & 2
• - spot UV elements (can be on both sides or just one, use your discretion)
• - colour pallet should match the logo file provided
• - incorporate tagline "where shine counts" (this tagline can be in a serif or sans serif font as long as it is complimentary to the overall design.
Nice to have
• - Premium elements with a clean design
Should not have
• - Please omit cartoon or whimsical like designs, think premium.
• - Colours should not stray from the pallet of the provided logo.

```html
<!DOCTYPE html>
<html lang="en">
<head>
<meta charset="utf-8">
<title>Brightway Haus Inc. Business Card</title>
<link rel="stylesheet" href="https://fonts.googleapis.com/css2?family=Open+Sans:wght@700;800&family=Roboto:wght@400;500;700&display=swap">
<style>
  :root {
    --backdrop: #2b2b2d;
    --teal: #12b8b8;
    --navy: #1c2657;
    --paper: #f3f3f3;
    --white: #ffffff;
  }
  html, body {
    margin: 0;
    width: 1200px;
    height: 960px;
    overflow: hidden;
    background: var(--backdrop);
  }
  .canvas { position: relative; width: 1200px; height: 960px; }
  .card {
    position: absolute;
    left: 320px;
    width: 600px;
    height: 342px;
    border-radius: 16px;
    overflow: hidden;
  }
  .card-front {
    top: 108px;
    background: var(--teal);
    display: flex;
    flex-direction: column;
    align-items: center;
    justify-content: center;
  }
  .front-name {
    font-family: "Open Sans", sans-serif;
    font-weight: 800;
    font-size: 40px;
    color: var(--white);
    letter-spacing: -0.5px;
    margin: 0;
    line-height: 1;
  }
  .front-tagline {
    font-family: "Roboto", sans-serif;
    font-size: 14px;
    color: var(--white);
    letter-spacing: 7px;
    margin: 12px 0 0;
  }
  .card-back { top: 493px; background: var(--navy); }
  .back-art { position: absolute; inset: 0; }
  .back-logo {
    position: absolute;
    left: 50px;
    top: 72px;
    display: flex;
    align-items: center;
    gap: 10px;
  }
  .logo-square { width: 34px; height: 34px; background: var(--teal); }
  .back-name {
    font-family: "Open Sans", sans-serif;
    font-weight: 800;
    font-size: 34px;
    color: var(--navy);
    letter-spacing: -0.5px;
    margin: 0;
  }
  .person {
    position: absolute;
    right: 28px;
    top: 172px;
    text-align: right;
    font-family: "Roboto", sans-serif;
  }
  .person-name { margin: 0; font-size: 20px; line-height: 24px; font-weight: 700; color: var(--teal); }
  .person-role { margin: 2px 0 0; font-size: 15px; line-height: 18px; font-weight: 700; color: var(--white); }
  .contact-list {
    position: absolute;
    right: 28px;
    top: 224px;
    margin: 0;
    padding: 0;
    list-style: none;
    font-family: "Roboto", sans-serif;
    font-size: 14px;
    color: var(--white);
    text-align: right;
  }
  .contact-list li { display: flex; justify-content: flex-end; align-items: center; gap: 8px; height: 19px; }
  .contact-list svg { width: 13px; height: 13px; fill: var(--teal); }
  .address {
    position: absolute;
    left: 222px;
    top: 282px;
    margin: 0;
    font-family: "Roboto", sans-serif;
    font-size: 14px;
    line-height: 19px;
    color: var(--white);
    font-style: normal;
  }
</style>
</head>
<body>
<div class="canvas">
  <section class="card card-front">
    <h1 class="front-name">BRIGHTWAY HAUS INC.</h1>
    <p class="front-tagline">Where Shine Counts</p>
  </section>

  <section class="card card-back">
    <svg class="back-art" viewBox="0 0 600 342" width="600" height="342" aria-hidden="true">
      <path d="M0,0 H530 C562,20 560,70 500,110 C420,160 200,262 80,270 C20,274 2,250 0,200 Z" fill="none" stroke="var(--white)" stroke-width="26"/>
      <path d="M0,0 H530 C562,20 560,70 500,110 C420,160 200,262 80,270 C20,274 2,250 0,200 Z" fill="none" stroke="var(--teal)" stroke-width="20"/>
      <path d="M0,0 H530 C562,20 560,70 500,110 C420,160 200,262 80,270 C20,274 2,250 0,200 Z" fill="var(--paper)"/>
    </svg>

    <div class="back-logo">
      <span class="logo-square"></span>
      <h2 class="back-name">BRIGHTWAY HAUS INC.</h2>
    </div>

    <div class="person">
      <p class="person-name">MARCUS HALE</p>
      <p class="person-role">CEO/FOUNDER</p>
    </div>

    <ul class="contact-list">
      <li>604 318 2750
        <svg viewBox="0 0 16 16"><path d="M3 1l3 3-2 2c1 2 3 4 5 5l2-2 3 3-2 3C7 15 1 9 1 3z"/></svg></li>
      <li>604 927 4416
        <svg viewBox="0 0 16 16"><path d="M4 0h8v16H4zM5.5 2v10h5V2zM7 13h2v1.5H7z" fill-rule="evenodd"/></svg></li>
      <li>604 318 2751
        <svg viewBox="0 0 16 16"><path d="M4 1h8v4H4zM1 6h14v7h-3v2H4v-2H1zM5 10v3h6v-3z" fill-rule="evenodd"/></svg></li>
      <li>hello@thebrightwayhaus.ca
        <svg viewBox="0 0 16 16"><path d="M1 3h14v10H1zM2 4l6 5 6-5z" fill-rule="evenodd"/></svg></li>
      <li>www.thebrightwayhaus.ca
        <svg viewBox="0 0 16 16"><circle cx="8" cy="8" r="7"/></svg></li>
    </ul>

    <address class="address">1420 Linden Court<br>Halden, Ontario 48215</address>
  </section>
</div>
</body>
</html>
```